Black Friday Specials for Car Styling Services and Products

I’m not sure of the exact design on this. Will leave to your creative talents. I’ve attached some of the other things we have done to help but need the black Friday vibe. More emphasis on the BF prices vs. the normal prices. Maybe use a starburst for special financing. Thanks.

Target Market(s)

Holiday Shoppers

Requirements
Must have
• Black Friday feel/look
Nice to have
• I like watermarked pictures as the back drop. See the other flyers I attached.

```html
<!DOCTYPE html>
<html lang="en">
<head>
<meta charset="utf-8">
<title>Black Friday Specials Flyer</title>
<link rel="stylesheet" href="https://fonts.googleapis.com/css2?family=Montserrat:ital,wght@0,600;0,700;0,800;1,700;1,800&family=Oswald:wght@500;600&family=Playfair+Display:wght@500&display=swap">
<style>
  :root{
    --page:#ffffff;
    --charcoal:#403f41;
    --yellow:#ffd200;
    --white:#ffffff;
    --red:#d8202a;
    --red-dark:#b5151d;
    --purple:#5a45a0;
    --purple-light:#6a56ad;
    --cyan:#00aeef;
    --amber:#fbb614;
    --ink:#1b1b1b;
  }
  *{margin:0;padding:0;box-sizing:border-box}
  html,body{width:1200px;height:1200px;overflow:hidden;background:var(--page)}
  body{font-family:"Montserrat",Arial,sans-serif;position:relative}

  .flyer{position:absolute;left:275px;top:139px;width:650px;height:922px;background:var(--charcoal);overflow:hidden}

  .brand{position:absolute;left:0;top:0;width:183px;height:66px;background:var(--white);border-radius:0 0 10px 0;display:flex;flex-direction:column;align-items:center;justify-content:center;gap:3px}
  .brand-name{font-weight:800;font-size:13px;color:var(--ink);letter-spacing:.5px;display:flex;align-items:center;gap:5px}
  .brand-name::before{content:"";width:8px;height:8px;background:var(--yellow)}
  .brand-tag{font-weight:800;font-size:5px;letter-spacing:1px;color:var(--ink)}

  .hero-photo{position:absolute;left:262px;top:-45px;width:400px;height:400px;border-radius:50%;border:13px solid var(--yellow);overflow:hidden;
    background:radial-gradient(circle at 58% 48%,#c8323a 0 18%,#8e1a22 35%,#6d6f72 60%,#a9a7a2 100%)}

  .bf-badge{position:absolute;left:200px;top:16px;width:174px;height:168px}
  .bf-badge .word-black{position:absolute;top:28px;width:100%;text-align:center;font-family:"Playfair Display",serif;font-size:58px;line-height:1;color:var(--white);transform:scaleX(.72)}
  .bf-badge .word-friday{position:absolute;top:96px;width:100%;text-align:center;font-family:"Oswald",sans-serif;font-weight:500;font-size:27px;color:var(--red);letter-spacing:-1px}

  .sale-tag{position:absolute;left:94px;top:135px;width:138px;height:64px;background:var(--red);transform:rotate(-28deg);clip-path:polygon(0 0,88% 0,100% 50%,88% 100%,0 100%);color:var(--white);display:flex;flex-direction:column;justify-content:center;padding-left:18px}
  .sale-tag .sale-word{font-weight:800;font-size:26px;line-height:1;font-style:italic}
  .sale-tag .sale-note{font-weight:700;font-size:7.5px;margin-left:30px}

  .tier-banner{position:absolute;left:25px;top:230px;width:337px;height:86px}
  .tier-banner ul{position:absolute;left:27px;top:17px;list-style:none;color:var(--white);font-weight:700;font-size:10.4px;line-height:16px}

  .promo-banner{position:absolute;left:23px;top:335px;width:506px;height:112px}
  .promo-banner p{position:absolute;left:52px;top:20px;width:400px;color:var(--white);font-weight:700;font-size:12.2px;line-height:16px}

  .savings-title{position:absolute;left:24px;top:472px;color:var(--white);font-weight:800;font-style:italic;font-size:16.2px;letter-spacing:.2px}

  .price-list{position:absolute;left:25px;top:513px;width:292px;height:344px;border:2px solid #c9a640;border-radius:18px;
    background:radial-gradient(circle at 45% 50%,var(--purple-light),var(--purple) 70%);box-shadow:4px 6px 10px rgba(0,0,0,.45);color:var(--white);font-weight:700;font-size:8.3px}
  .item{position:absolute;left:16px;right:12px}
  .item .now{position:absolute}
  .item .was{position:absolute;right:0;text-decoration:line-through}
  .was{text-decoration:line-through;text-decoration-thickness:1px}

  .package-card{position:absolute;border:3px solid var(--yellow);box-shadow:5px 7px 10px rgba(0,0,0,.5);border-radius:26px 2px 60px 44px;color:var(--white);text-align:center;font-weight:700}
  .package-card h2{font-family:"Oswald",sans-serif;font-weight:600;font-size:35px;line-height:1;margin-top:10px;transform:scaleX(.85);color:var(--white)}
  .package-card .tiers{position:relative;height:90px;font-size:10px}
  .package-card .tier{position:absolute}
  .package-card .tier-label{color:var(--white)}
  .package-card .tier-price{color:var(--ink);margin-top:9px;word-spacing:8px}
  .remote-start{left:356px;top:523px;width:258px;height:157px;background:var(--cyan)}
  .subwoofer-truck{left:360px;top:700px;width:248px;height:150px;background:var(--amber)}

  .fine-print{position:absolute;left:22px;top:874px;width:615px;color:var(--white);font-weight:700;font-style:italic;font-size:6.3px;line-height:10px}
</style>
</head>
<body>
<main class="flyer">

  <div class="hero-photo" role="img" aria-label="Close-up photo of a glossy red sports car's rear wheel on a paved driveway"></div>

  <div class="brand">
    <div class="brand-name">GLIDE SHADE</div>
    <div class="brand-tag">AUTO STYLING STUDIOS</div>
  </div>

  <div class="bf-badge">
    <svg width="174" height="168" viewBox="0 0 174 168" aria-hidden="true">
      <defs>
        <linearGradient id="hexFill" x1="0" y1="0" x2="1" y2="1">
          <stop offset="0" stop-color="#4a4a4c"/><stop offset=".5" stop-color="#151515"/><stop offset="1" stop-color="#3a3a3c"/>
        </linearGradient>
      </defs>
      <polygon points="87,0 174,42 174,126 87,168 0,126 0,42" fill="var(--yellow)"/>
      <polygon points="87,9 166,47 166,121 87,159 8,121 8,47" fill="url(#hexFill)"/>
    </svg>
    <div class="word-black">Black</div>
    <div class="word-friday">FRIDAY</div>
  </div>

  <div class="sale-tag">
    <span class="sale-word">SALE</span>
    <span class="sale-note">upto 25% off</span>
  </div>

  <section class="tier-banner">
    <svg width="337" height="86" viewBox="0 0 337 86" aria-hidden="true">
      <polygon points="0,0 312,0 337,43 312,86 0,86" fill="var(--yellow)"/>
      <polygon points="4,4 310,4 332,43 310,82 4,82" fill="var(--white)"/>
      <polygon points="12,9 304,9 323,43 304,77 12,77" fill="var(--red)" stroke="var(--yellow)" stroke-width="2"/>
    </svg>
    <ul>
      <li>Purchases up to $249.99 get 10% off</li>
      <li>Purchases between $250 and $650 get 15% off</li>
      <li>Purchases of $650+ get 20% off</li>
    </ul>
  </section>

  <section class="promo-banner">
    <svg width="506" height="112" viewBox="0 0 506 112" aria-hidden="true">
      <polygon points="0,0 470,0 506,56 470,112 0,112" fill="var(--yellow)"/>
      <polygon points="4,4 467,4 500,56 467,108 4,108" fill="var(--white)"/>
      <polygon points="20,12 456,12 484,56 456,100 20,100" fill="var(--purple)" stroke="var(--yellow)" stroke-width="3"/>
    </svg>
    <p>Incredible deals on window tint, paint protection film, color change wraps and ceramic coating!<br>PLUS, SPECIAL 90 DAY, NO INTEREST PAYMENT PLAN FOR PURCHASES OVER $650**.</p>
  </section>

  <h1 class="savings-title">Other Great Black Friday Savings (installation included!!):</h1>

  <section class="price-list">
    <div class="item" style="top:30px">Dash Cam&nbsp; 2K QHD, LTE + GPS + WiFi<span class="now" style="left:194px">$459</span><span class="was">$579</span></div>
    <div class="item" style="top:64px">Dash Cam&nbsp; 1080p Full HD, Wifi,<span class="now" style="left:196px">$299</span><span class="was">$399</span></div>
    <div class="item" style="top:98px">Amplifier Upgrade 1,500-Watt Subwoofer amp<br><span class="now" style="left:194px;top:10px">$549</span><span class="was" style="top:10px">$699</span></div>
    <div class="item" style="top:146px;left:14px">Amplifier Upgrade 500-Watt 4-speaker amp<br><span class="now" style="left:196px;top:10px">$37</span><span class="was" style="top:10px">$499</span></div>
    <div class="item" style="top:200px;left:14px">Underbody Glow&nbsp;&nbsp;&nbsp; Chasing Lighting<span class="now" style="left:192px">$349</span><span class="was">$455</span></div>
    <div class="item" style="top:250px;left:13px">Wheel Well Lights 8-Piece Rock Light<span class="now" style="left:191px">$299</span><span class="was">$399</span></div>
    <div class="item" style="top:292px;left:11px">Marine Upgrade<br>tweeter array<span class="now" style="left:95px;top:0">Dual 10”, 300-Watt tower speakers/</span><span class="now" style="left:195px;top:20px">$1,699</span><span class="was" style="top:20px">$1,899</span></div>
  </section>

  <section class="package-card remote-start">
    <h2>Remote Start</h2>
    <div class="tiers">
      <div class="tier" style="left:12px;top:8px"><div class="tier-label">Premium package</div><div class="tier-price"><span class="was">$349</span> $299</div></div>
      <div class="tier" style="left:136px;top:7px"><div class="tier-label">Super package</div><div class="tier-price"><span class="was">$479</span> $399</div></div>
      <div class="tier" style="left:70px;top:49px"><div class="tier-label">Ultimate&nbsp; package</div><div class="tier-price"><span class="was">$679</span> $599</div></div>
    </div>
  </section>

  <section class="package-card subwoofer-truck">
    <h2>Subwoofer Truck</h2>
    <div class="tiers">
      <div class="tier" style="left:10px;top:6px"><div class="tier-label">Premium package</div><div class="tier-price"><span class="was">$849</span> $749</div></div>
      <div class="tier" style="left:128px;top:5px"><div class="tier-label">Super package</div><div class="tier-price"><span class="was">$1,149</span> $999</div></div>
      <div class="tier" style="left:68px;top:46px"><div class="tier-label">Ultimate&nbsp; package</div><div class="tier-price"><span class="was">$1,489</span> $1,299</div></div>
    </div>
  </section>

  <footer class="fine-print">
    *Pricing available until December 1<br>
    **Special 90-day payment plan:&nbsp; Only ½ due at the time of purchase.&nbsp; The balance is due in three equal payments over 30, 60 and 90 days.<br>
    For example, for a $500 purchase only $250 is due at the time of the sale.&nbsp; Then three equal payments of $83.33 at 30, 60 and 90 days.<br>
    Limited availability.
  </footer>

</main>
</body>
</html>
```